Verdant Ledger - Paid Surveys publisher portal

• Homepage
• Blank Sub Page (Where content goes in between the header/footer)
• Publisher Application Page, complete with Form
• Survey Wall page

Sites that are in a similar vertical that have interesting designs:
rovabin.com
quillmarsh.com
dovek.com
tarn.io

This is a business-to-business site, and needs to have this type of feel to it. Focus on generating revenue, offer completion, paid surveys is the market.

Format: HTML/CSS

Link to current version of application, and form:
https://gridwaveform.brokelqest.com
https://gridwaveform.brokelqest.com/apply
https://gridwaveform.brokelqest.com/panel/4/morvath_user

Please note that we are changing the brand of this project, the name will be determined shortly but everything else remains. It will likely be Verdant Ledger instead of GridWaveform. We will confirm.

Industry/Entity Type

Market Research

Coding

Coded - Design and coding required

Number of Pages Required

4 page

Font styles to use
Sans Serif

Colors

Designer to choose colors to be used in the design.

```html
<!DOCTYPE html>
<html lang="en">
<head>
<meta charset="utf-8">
<title>GridWaveform – Paid Surveys Publisher Portal</title>
<link rel="stylesheet" href="https://fonts.googleapis.com/css2?family=Roboto+Condensed:wght@400;700&family=Open+Sans:wght@400;600;700&display=swap">
<style>
:root{
  --red:#e8413a;
  --red-dark:#d4322c;
  --ink:#1f1f1f;
  --text:#555;
  --muted:#8a8a8a;
  --line:#e3e3e3;
  --strip:#ececec;
  --blue:#1f7fd1;
  --blue-deep:#1566b4;
  --hero-title:#1e7ac8;
  --footer:#0d0d0d;
  --footer-bottom:#050505;
  --white:#fff;
  --star:#f2a516;
}
*{box-sizing:border-box;margin:0;padding:0}
html,body{width:1200px;height:4054px;overflow:hidden}
body{font-family:'Open Sans',Arial,sans-serif;color:var(--text);background:var(--white);position:relative}
.section{position:absolute;left:0;width:1200px;overflow:hidden}
.abs{position:absolute}
h1,h2,h3,.heading{font-family:'Roboto Condensed',Arial,sans-serif;font-weight:400;color:var(--ink)}
.btn{position:absolute;display:flex;align-items:center;justify-content:center;border-radius:18px;font-size:16px;background:var(--red);color:var(--white);font-family:'Open Sans',Arial,sans-serif}
.btn--ghost{background:var(--white);color:var(--ink);border:1px solid #9a9a9a}
.para{position:absolute;font-size:13px;line-height:26px;color:var(--text)}

/* header */
.site-header{top:0;height:103px;background:var(--white);border-top:6px solid var(--red);box-shadow:0 2px 6px rgba(0,0,0,.12);z-index:3}
.brand{left:90px;top:22px;display:flex;align-items:center;gap:14px}
.brand__dot{width:60px;height:60px;border-radius:50%;background:var(--red)}
.brand__name{font-family:'Roboto Condensed',Arial,sans-serif;font-weight:700;font-size:32px;color:var(--ink)}
.nav{right:88px;top:36px;display:flex;gap:36px;font-size:17px;color:var(--ink)}
.nav .active{color:var(--red)}

/* hero */
.hero{top:103px;height:554px}
.hero__photo{position:absolute;inset:0;background:linear-gradient(90deg,#dfe6ef 0%,#cfd9e5 35%,#9aa9b9 55%,#6f7f91 75%,#b9c6d3 100%)}
.hero__title{left:86px;top:145px;font-size:82px;color:var(--hero-title);font-family:'Roboto Condensed',Arial,sans-serif}
.hero__lead{left:88px;top:238px;font-size:38px;line-height:48px;color:var(--ink);font-family:'Roboto Condensed',Arial,sans-serif}
.hero__arrows{left:88px;top:358px;display:flex;gap:6px}
.arrow-dot{width:30px;height:30px;border-radius:50%;background:#555;display:flex;align-items:center;justify-content:center}

/* partner strip */
.partners{top:657px;height:154px;background:var(--strip)}
.partner{top:30px;width:162px;height:91px;background:#f7f7f7;border:1px solid #dadada;display:flex;align-items:center;justify-content:center}
.partner span{display:block;width:92px;height:16px;background:#bdbdbd;border-radius:3px}

/* about */
.about{top:811px;height:532px}
.about__frame{left:97px;top:100px;width:411px;height:267px;border:4px solid #1a1a1a}
.about__photo{left:127px;top:121px;width:397px;height:317px;background:linear-gradient(135deg,#c9a27a,#8f6c4f 45%,#5f6e7a 70%,#d7d2cb);box-shadow:0 6px 16px rgba(0,0,0,.25)}
.about h2{left:565px;top:128px;font-size:36px}

/* services */
.services{top:1343px;height:582px}
.services__photo{position:absolute;inset:0;background:linear-gradient(120deg,#e6eef7 0%,#c9d8e8 40%,#e8d8c6 62%,#b9cde0 80%,#dbe5ef 100%)}
.services h2{left:0;width:1200px;top:74px;text-align:center;font-size:36px}
.svc-card{top:236px;width:313px;height:254px;background:var(--white);box-shadow:0 4px 14px rgba(0,0,0,.12)}
.svc-icon{top:170px;width:120px;height:120px;border-radius:50%;display:flex;align-items:center;justify-content:center}
.svc-icon--blue{background:#2f8fdc}
.svc-icon--red{background:var(--red)}
.svc-card h3{position:absolute;top:90px;width:100%;text-align:center;font-family:'Open Sans',Arial,sans-serif;font-weight:700;font-size:20px}
.svc-card p{position:absolute;top:125px;left:30px;right:30px;text-align:center;font-size:14px;line-height:25px;color:var(--text)}
.svc-card .btn{top:233px;left:102px;width:110px;height:30px;font-size:14px}
.svc-arrow{top:340px;width:30px;height:30px;border-radius:50%;background:rgba(255,255,255,.85);border:1px solid #bbb;display:flex;align-items:center;justify-content:center}

/* network */
.network{top:1925px;height:589px}
.network h2{left:100px;top:150px;font-size:36px}
.network__frame{left:687px;top:108px;width:410px;height:305px;border:4px solid #1a1a1a}
.network__photo{left:670px;top:135px;width:400px;height:313px;background:linear-gradient(135deg,#eef1ea,#c9d4c2 40%,#9aa68f 65%,#e6e2d8);box-shadow:0 6px 16px rgba(0,0,0,.25)}

/* testimonials */
.testimonials{top:2514px;height:500px;background:linear-gradient(180deg,var(--blue) 0%,#2b8ad8 50%,var(--blue-deep) 100%)}
.testimonials h2{left:0;width:1200px;top:72px;text-align:center;font-size:38px;color:var(--white)}
.tcard{top:181px;width:450px;height:224px;background:var(--white);box-shadow:0 4px 12px rgba(0,0,0,.2)}
.tcard__avatar{top:235px;width:124px;height:124px;border-radius:50%;border:5px solid var(--white);background:linear-gradient(160deg,#d9c1a8,#8a6a52)}
.tcard__quote{position:absolute;right:30px;top:8px;font-family:Georgia,serif;font-size:100px;line-height:100px;color:var(--red);font-weight:700}
.tcard p{position:absolute;left:140px;right:24px;top:74px;font-size:12.5px;line-height:23px;color:#777}
.tcard__stars{position:absolute;left:140px;top:168px;color:var(--star);font-size:14px;letter-spacing:2px}
.tcard__name{position:absolute;right:46px;top:166px;color:#f08a2a;font-size:17px}
.testimonials__bar{left:355px;top:457px;width:140px;height:6px;background:rgba(255,255,255,.25);border-radius:3px}

/* news */
.news{top:3014px;height:595px}
.news h2{left:0;width:1200px;top:82px;text-align:center;font-size:40px}
.news-item{top:189px;width:311px}
.news-item__photo{height:170px;background:linear-gradient(135deg,#b7c7d6,#4f6276 55%,#d1d9e1)}
.news-item__meta{display:flex;gap:4px;margin-top:17px}
.news-tag{background:var(--red);color:var(--white);font-size:11px;padding:0 10px;height:19px;line-height:19px}
.news-comments{background:#222;width:36px;height:19px;display:flex;align-items:center;justify-content:center}
.news-item h3{font-family:'Open Sans',Arial,sans-serif;font-size:18px;color:#333;margin-top:16px}
.news-item p{font-size:12.5px;line-height:18px;color:#666;margin-top:6px}
.news-item .more{font-size:12.5px;color:var(--red);margin-top:8px;display:block}

/* footer */
.site-footer{top:3609px;height:378px;background:var(--footer);border-top:8px solid var(--blue)}
.footer-col{top:97px}
.footer-col h4{font-family:'Open Sans',Arial,sans-serif;font-weight:400;font-size:19px;color:var(--white);letter-spacing:.5px}
.footer-col ul{list-style:none;margin-top:21px}
.footer-col li{font-size:16px;color:#ddd;line-height:33px}
.contact-row{display:flex;gap:12px;margin-top:22px}
.contact-row b{display:block;font-size:16px;color:var(--white);font-weight:600}
.contact-row small{display:block;font-size:15px;color:#ccc}
.field{left:797px;width:309px;height:38px;background:var(--white);font-size:15px;color:#666;padding:8px 14px}
.send{left:797px;top:272px;width:125px;height:35px;background:var(--red);color:var(--white);font-size:17px;display:flex;align-items:center;justify-content:center}
.footer-bottom{top:3987px;height:67px;background:var(--footer-bottom);color:#888;font-size:13px;display:flex;align-items:center;justify-content:center}
</style>
</head>
<body>

<header class="section site-header">
  <div class="abs brand"><span class="brand__dot"></span><span class="brand__name">GridWaveform</span></div>
  <nav class="abs nav"><span class="active">Home</span><span>About us</span><span>Services</span><span>Products</span><span>Faq</span><span>News</span><span>Contact us</span></nav>
</header>

<section class="section hero">
  <div class="hero__photo" role="img" aria-label="Two business colleagues reviewing a tablet in a bright office"></div>
  <h1 class="abs hero__title">GridWaveform</h1>
  <p class="abs hero__lead">We generate revenue,offer<br>completion,paid surveys</p>
  <div class="abs hero__arrows">
    <span class="arrow-dot"><svg width="12" height="12" viewBox="0 0 12 12"><path d="M8 2 4 6l4 4" stroke="#fff" stroke-width="2" fill="none"/></svg></span>
    <span class="arrow-dot"><svg width="12" height="12" viewBox="0 0 12 12"><path d="M4 2l4 4-4 4" stroke="#fff" stroke-width="2" fill="none"/></svg></span>
  </div>
</section>

<section class="section partners" aria-label="Partners">
  <div class="abs partner" style="left:165px"><span></span></div>
  <div class="abs partner" style="left:342px"><span></span></div>
  <div class="abs partner" style="left:519px"><span></span></div>
  <div class="abs partner" style="left:697px"><span></span></div>
  <div class="abs partner" style="left:876px"><span></span></div>
</section>

<section class="section about">
  <div class="abs about__frame"></div>
  <div class="abs about__photo" role="img" aria-label="Desk seen from above with a laptop showing a survey, coffee and a tablet"></div>
  <h2 class="abs">About us</h2>
  <p class="para" style="left:565px;top:196px;width:540px">It is a long established fact that a reader will be distracted by the readable content of a page when looking at its layout. The point of using Lorem Ipsum is that it has a more-or-less normal distribution of letters, as opposed to using 'Content here, content here', making it look like readable English. Many desktop publishing packages and web page editors now use Lorem Ipsum as their default model text, and a search for 'lorem ipsum' will uncover many</p>
  <span class="btn" style="left:565px;top:392px;width:124px;height:36px">Read More</span>
</section>

<section class="section services">
  <div class="services__photo" role="img" aria-label="Business person holding a phone over a blurred city skyline"></div>
  <h2 class="abs">Our Services</h2>
  <span class="abs svc-arrow" style="left:47px"><svg width="10" height="10" viewBox="0 0 10 10"><path d="M7 1 3 5l4 4" stroke="#666" stroke-width="1.6" fill="none"/></svg></span>
  <span class="abs svc-arrow" style="left:1118px"><svg width="10" height="10" viewBox="0 0 10 10"><path d="M3 1l4 4-4 4" stroke="#666" stroke-width="1.6" fill="none"/></svg></span>

  <article class="abs svc-card" style="left:100px">
    <h3>Affiliates</h3>
    <p>It is a long established fact that a reader will be distracted by the readable content of a page</p>
    <span class="btn btn--ghost">Read more</span>
  </article>
  <article class="abs svc-card" style="left:443px">
    <h3>Surveys</h3>
    <p>It is a long established fact that a reader will be distracted by the readable content of a page</p>
    <span class="btn">Read more</span>
  </article>
  <article class="abs svc-card" style="left:790px">
    <h3>Advertisers</h3>
    <p>It is a long established fact that a reader will be distracted by the readable content of a page</p>
    <span class="btn btn--ghost">Read more</span>
  </article>

  <div class="abs svc-icon svc-icon--blue" style="left:196px">
    <svg width="58" height="58" viewBox="0 0 58 58" fill="none" stroke="#fff" stroke-width="2.5"><circle cx="29" cy="14" r="7"/><circle cx="11" cy="44" r="6"/><circle cx="47" cy="44" r="6"/><path d="M29 21v10M29 31 13 38M29 31l16 7"/></svg>
  </div>
  <div class="abs svc-icon svc-icon--red" style="left:540px">
    <svg width="58" height="58" viewBox="0 0 58 58" fill="none" stroke="#fff" stroke-width="2.5"><rect x="14" y="8" width="30" height="42" rx="2"/><path d="M20 18h18M20 26h18M20 34h12M20 42h8"/></svg>
  </div>
  <div class="abs svc-icon svc-icon--blue" style="left:886px">
    <svg width="58" height="58" viewBox="0 0 58 58" fill="none" stroke="#fff" stroke-width="2.5"><path d="M10 24h8l20-12v34L18 34h-8z"/><path d="M16 34l4 12h6l-3-12M44 22c4 3 4 11 0 14"/></svg>
  </div>
</section>

<section class="section network">
  <h2 class="abs">Your network. Your platform.</h2>
  <p class="para" style="left:100px;top:216px;width:540px">It is a long established fact that a reader will be distracted by the readable content of a page when looking at its layout. The point of using Lorem Ipsum is that it has a more-or-less normal distribution of letters, as opposed to using 'Content here, content here', making it look like readable English. Many desktop publishing packages and web page editors now use Lorem Ipsum as their default model text, and a search for 'lorem ipsum' will uncover many</p>
  <span class="btn" style="left:100px;top:412px;width:124px;height:36px">Read More</span>
  <div class="abs network__frame"></div>
  <div class="abs network__photo" role="img" aria-label="Woman working on a laptop at a bright office desk"></div>
</section>

<section class="section testimonials">
  <h2 class="abs">Testimonials</h2>
  <article class="abs tcard" style="left:127px">
    <span class="tcard__quote">“</span>
    <p>The point of using Lorem Ipsum is that it has a more-or-less normal distribution of letters, as opposed to using 'Content</p>
    <span class="tcard__stars">★★★★☆</span>
    <span class="tcard__name">-&nbsp;&nbsp;&nbsp;Helen</span>
  </article>
  <div class="abs tcard__avatar" style="left:88px" role="img" aria-label="Portrait of a smiling client"></div>
  <article class="abs tcard" style="left:646px">
    <span class="tcard__quote">“</span>
    <p>The point of using Lorem Ipsum is that it has a more-or-less normal distribution of letters, as opposed to using 'Content</p>
    <span class="tcard__stars">★★★★☆</span>
    <span class="tcard__name">- Amet</span>
  </article>
  <div class="abs tcard__avatar" style="left:611px" role="img" aria-label="Portrait of a client wearing sunglasses"></div>
  <div class="abs testimonials__bar"></div>
</section>

<section class="section news">
  <h2 class="abs">Latest News</h2>
  <article class="abs news-item" style="left:95px">
    <div class="news-item__photo" role="img" aria-label="Businessman walking toward a bright city window"></div>
    <div class="news-item__meta"><span class="news-tag">Dec 03</span><span class="news-comments"><svg width="16" height="10" viewBox="0 0 16 10"><rect x="1" y="1" width="10" height="6" rx="2" fill="#fff"/><path d="M13 3h2v5h-2v2l-2-2H8" stroke="#fff" fill="none"/></svg></span></div>
    <h3>Neque porro quisquam dolorem</h3>
    <p>It has survived not only five centuries, but also the leap into electronic typesetting.</p>
    <span class="more">Read More »</span>
  </article>
  <article class="abs news-item" style="left:443px">
    <div class="news-item__photo" role="img" aria-label="Team meeting around a laptop" style="background:linear-gradient(135deg,#8da0b3,#3d4b5a 55%,#a9b7c4)"></div>
    <div class="news-item__meta"><span class="news-tag">Dec 03</span><span class="news-comments"><svg width="16" height="10" viewBox="0 0 16 10"><rect x="1" y="1" width="10" height="6" rx="2" fill="#fff"/><path d="M13 3h2v5h-2v2l-2-2H8" stroke="#fff" fill="none"/></svg></span></div>
    <h3>Porro quisquam est qui</h3>
    <p>It has survived not only five centuries, but also the leap into electronic typesetting.</p>
    <span class="more">Read More »</span>
  </article>
  <article class="abs news-item" style="left:795px">
    <div class="news-item__photo" role="img" aria-label="Two colleagues discussing documents at a desk" style="background:linear-gradient(135deg,#cdd8e2,#6f8293 55%,#e0e6ec)"></div>
    <div class="news-item__meta"><span class="news-tag">Dec 03</span><span class="news-comments"><svg width="16" height="10" viewBox="0 0 16 10"><rect x="1" y="1" width="10" height="6" rx="2" fill="#fff"/><path d="M13 3h2v5h-2v2l-2-2H8" stroke="#fff" fill="none"/></svg></span></div>
    <h3>Dolorem ipsum quia dolor</h3>
    <p>It has survived not only five centuries, but also the leap into electronic typesetting.</p>
    <span class="more">Read More »</span>
  </article>
</section>

<footer class="section site-footer">
  <div class="abs footer-col" style="left:95px">
    <h4>CONTACT US</h4>
    <div class="contact-row">
      <svg width="20" height="16" viewBox="0 0 20 16" fill="none" stroke="#fff" stroke-width="1.6"><rect x="1" y="2" width="18" height="12"/><path d="M1 2l9 7 9-7"/></svg>
      <div><b>EMAIL ADDRESS</b><small>info@rovelmark.com</small></div>
    </div>
    <div class="contact-row">
      <svg width="20" height="20" viewBox="0 0 20 20" fill="none" stroke="#fff" stroke-width="1.6"><path d="M4 2l4 1 1 4-2 2c1 2 3 4 5 5l2-2 4 1 1 4c-8 1-16-7-15-15z"/></svg>
      <div><b>PHONE NUMBER</b><small>(555) 014-2290</small></div>
    </div>
  </div>
  <div class="abs footer-col" style="left:365px">
    <h4>ABOUT</h4>
    <ul><li>Home</li><li>About Us</li><li>Services</li><li>Products</li></ul>
  </div>
  <div class="abs footer-col" style="left:568px">
    <h4>RESOURCES</h4>
    <ul><li>News</li><li>Support</li><li>Faq</li><li>Contact</li></ul>
  </div>
  <div class="abs footer-col" style="left:792px">
    <h4>GET IN TOUCH</h4>
  </div>
  <div class="abs field" style="top:132px">Your Name</div>
  <div class="abs field" style="top:175px">Email address</div>
  <div class="abs field" style="top:221px">Phone</div>
  <div class="abs send">SEND</div>
</footer>
<div class="section footer-bottom">© 2018 Company Name &nbsp;All right reserved</div>

</body>
</html>
```